Calvanto Group Real Estate Company business cards

New business card design, we are generally happy with the basic layout of the existing front of business card, (feel free to change) but require a head shot photo on the back side.

http://www.calvanto.com.au/

Attached logos, and existing business card

------------------------------

Target Market(s)

Real estate

Industry/Entity Type

Real Estate

Contact Information for Business Card

Standard size double sided

Font styles to use
Other font styles liked:
• Futura

Requirements
Must have
• Photo head shot on the back side
Nice to have
• yes
Should not have
• No

```html
<!DOCTYPE html>
<html lang="en">
<head>
<meta charset="utf-8">
<title>Calvanto Group – Business Cards</title>
<link href="https://fonts.googleapis.com/css2?family=Jost:wght@400;500&family=Arimo:wght@400;700&display=swap" rel="stylesheet">
<style>
  :root {
    --bg: #e9e6e1;
    --purple: #2e2160;
    --orange: #e8891c;
    --card-white: #f1f1f1;
    --ink: #1e1e1e;
    --rule: #4a4a4a;
    --headshot-wall: #e4e6e9;
    --headshot-suit: #2b3040;
    --lock-metal: #b3b5c0;
    --key-gold: #d9962a;
  }
  * { margin: 0; padding: 0; box-sizing: border-box; }
  html, body { width: 1200px; height: 909px; overflow: hidden; }
  body {
    background: var(--bg);
    position: relative;
    font-family: "Arimo", Arial, sans-serif;
  }
  .card {
    position: absolute;
    top: 284px;
    width: 560px;
    height: 340px;
    border-radius: 4px;
    overflow: hidden;
    box-shadow: 0 8px 22px rgba(0,0,0,.22);
  }
  .card-back { left: 30px; background: var(--purple); }
  .card-front { left: 610px; background: var(--card-white); }
  .card-back svg { position: absolute; inset: 0; }

  .wordmark {
    font-family: "Jost", "Futura", sans-serif;
    font-weight: 500;
    letter-spacing: -0.5px;
    line-height: 1;
    position: absolute;
  }
  .wordmark-tag {
    font-family: "Jost", "Futura", sans-serif;
    font-weight: 500;
    letter-spacing: 5px;
    font-size: 9px;
    position: absolute;
  }
  .card-back .wordmark { color: var(--orange); font-size: 54px; left: 236px; top: 212px; }
  .card-back .wordmark-tag { color: var(--orange); font-size: 9px; left: 438px; top: 270px; }

  .card-front .wordmark { color: var(--purple); font-size: 58px; left: 0; right: 0; text-align: center; top: 34px; }
  .card-front .wordmark-tag { color: var(--purple); left: 354px; top: 98px; }

  .contact { position: absolute; left: 0; right: 0; top: 120px; text-align: center; color: var(--ink); }
  .contact-name { font-weight: 700; font-size: 28px; line-height: 32px; color: var(--orange); }
  .contact-role { font-size: 16px; line-height: 20px; }
  .contact-lines { font-size: 16px; line-height: 20px; margin-top: 14px; }
  .contact-abn { font-size: 16px; line-height: 20px; margin-top: 14px; }

  .edge-rule { position: absolute; height: 2px; background: var(--rule); }
  .edge-rule.left { left: 0; width: 140px; top: 232px; }
  .edge-rule.right { right: 0; width: 170px; top: 306px; }
</style>
</head>
<body>
  <section class="card card-back" aria-label="Card back">
    <svg viewBox="0 0 560 340" width="560" height="340">
      <defs>
        <radialGradient id="headshotTone" cx="0.78" cy="1" r="0.75">
          <stop offset="0" stop-color="var(--headshot-suit)"/>
          <stop offset="0.45" stop-color="#5b6070"/>
          <stop offset="0.75" stop-color="#cfd2d8"/>
          <stop offset="1" stop-color="var(--headshot-wall)"/>
        </linearGradient>
        <radialGradient id="lockTone" cx="0.55" cy="0.35" r="0.8">
          <stop offset="0" stop-color="var(--key-gold)" stop-opacity=".55"/>
          <stop offset="0.35" stop-color="var(--lock-metal)"/>
          <stop offset="1" stop-color="#8a8c9c"/>
        </radialGradient>
      </defs>
      <g role="img" aria-label="Head shot photo of the director in a dark suit and blue tie">
        <path d="M290 0 H560 V168 Q440 138 312 168 Q312 80 290 0 Z" fill="url(#headshotTone)"/>
      </g>
      <g role="img" aria-label="Photo of a gold key in a silver door lock">
        <path d="M0 190 Q110 172 200 182 Q186 262 222 340 H0 Z" fill="url(#lockTone)"/>
      </g>
    </svg>
    <div class="wordmark">calvanto</div>
    <div class="wordmark-tag">GROUP</div>
  </section>

  <section class="card card-front" aria-label="Card front">
    <div class="wordmark">calvanto</div>
    <div class="wordmark-tag">GROUP</div>
    <div class="contact">
      <div class="contact-name">Daniel Tran</div>
      <div class="contact-role">Director</div>
      <div class="contact-lines">
        <div>0412 555 018</div>
        <div>www.calvanto.com.au</div>
        <div>daniel.tran@calvanto.com.au</div>
      </div>
      <div class="contact-abn">ABN: 41 208 663 907</div>
    </div>
    <span class="edge-rule left"></span>
    <span class="edge-rule right"></span>
  </section>
</body>
</html>
```